High-end construction company needs a business card design

We need a modern looking business card that draws people in, is memorable and looks so good people will want to sick it on their fridges.
On the first side what is needed are:
Logo
My name - Tomasz Brelwik
Title - Managing Director
Website - www.varkelt.co.uk
Email - tomasz@varkelt.co.uk
Telephone - 020 5194 6281
Mobile - 07845139072
On the back side was is needed is a list of all the services we provide:
-Kitchen Renovations
-Bathroom Renovations
-House Renovations
-Garage Conversions
-Extensions
-Loft Conversions
-Conservatories
-Carpentry
-Tiling
-Electrical
-Plumbing & Heating
-Bricklaying
-Landscaping
-Decorating
-Plastering
We would like the colours to be the same shades as on the logo with grey or black for the words.
Target Market(s)
Anyone who needs building work done
Contact Information for Business Card
This business card is for a construction company which strives to deliver excellent service and quality.
The look and feel of the card should represent this.
Requirements
Must have
- On the first side what is needed are:
Logo
My name - Tomasz Brelwik
Title - Managing Director
Website - www.varkelt.co.uk
Email - tomasz@varkelt.co.uk
Telephone - 020 5194 6281
Mobile - 07845139072
Nice to have
- Cool looking features

```html
<!DOCTYPE html>
<html lang="en">
<head>
<meta charset="utf-8">
<title>Varkelt Construction Ltd – Business Card</title>
<link href="https://fonts.googleapis.com/css2?family=Montserrat:wght@400;500;600;700&display=swap" rel="stylesheet">
<style>
  :root {
    --page-bg: #1b1b1b;
    --card-bg: #2a2a2a;
    --card-edge: #333333;
    --brand-green: #5cbf3a;
    --text-light: #f2f2f2;
    --text-grey: #9a9a9a;
  }
  * { margin: 0; padding: 0; box-sizing: border-box; }
  html, body {
    width: 1200px; height: 900px; overflow: hidden;
    background: var(--page-bg);
    font-family: "Montserrat", sans-serif;
  }
  .canvas {
    position: relative; width: 1200px; height: 900px;
    display: flex; flex-direction: column; align-items: center;
    justify-content: center; gap: 36px;
  }
  .card {
    position: relative; width: 720px; height: 400px;
    background: linear-gradient(135deg, #2d2d2d 0%, var(--card-bg) 55%, #242424 100%);
    border: 1px solid var(--card-edge);
    box-shadow: 0 18px 40px rgba(0,0,0,0.55);
  }
  /* Back: services */
  .services {
    position: absolute; left: 52px; top: 34px; list-style: none;
    color: var(--text-light); font-size: 17px; font-weight: 500; line-height: 22px;
  }
  .services li { display: flex; align-items: center; gap: 14px; }
  .services li::before {
    content: ""; width: 8px; height: 8px; border-radius: 50%;
    background: var(--brand-green); flex: none;
  }
  .brand-name {
    position: absolute; font-weight: 700; letter-spacing: 1px;
    display: flex; align-items: flex-start; gap: 14px;
    font-size: 30px; line-height: 38px;
  }
  .brand-name .brand-mark { width: 18px; height: 18px; flex: none; margin-top: 10px; }
  .card-back .brand-name { left: 400px; top: 170px; color: var(--text-grey); }
  .card-back .brand-mark { background: var(--text-grey); }
  /* Front: contact */
  .card-front .brand-name { left: 36px; top: 160px; color: var(--brand-green); }
  .card-front .brand-mark { background: var(--brand-green); }
  .divider {
    position: absolute; left: 410px; top: 70px; width: 2px; height: 260px;
    background: var(--brand-green);
  }
  .contact {
    position: absolute; left: 446px; top: 80px; color: var(--text-light);
  }
  .contact-name { font-size: 29px; font-weight: 600; color: var(--brand-green); line-height: 34px; }
  .contact-title { font-size: 19px; font-weight: 500; margin-bottom: 18px; }
  .contact-address { font-size: 19px; line-height: 25px; margin-bottom: 14px; }
  .contact-lines { list-style: none; font-size: 19px; line-height: 28px; }
  .contact-lines li { display: flex; align-items: center; gap: 10px; }
  .contact-lines svg { width: 14px; height: 14px; flex: none; }
</style>
</head>
<body>
<main class="canvas">

  <section class="card card-back" aria-label="Card back: services">
    <ul class="services">
      <li>Kitchen Renovations</li>
      <li>Bathroom Renovations</li>
      <li>House Renovations</li>
      <li>Garage Conversions</li>
      <li>Extensions</li>
      <li>Loft Conversions</li>
      <li>Conservatories</li>
      <li>Carpentry</li>
      <li>Tiling</li>
      <li>Electrical</li>
      <li>Plumbing &amp; Heating</li>
      <li>Bricklaying</li>
      <li>Landscaping</li>
      <li>Decorating</li>
      <li>Plastering</li>
    </ul>
    <div class="brand-name"><span class="brand-mark"></span><span class="brand-text">Varkelt<br>Construction Ltd</span></div>
  </section>

  <section class="card card-front" aria-label="Card front: contact details">
    <div class="brand-name"><span class="brand-mark"></span><span class="brand-text">Varkelt<br>Construction Ltd</span></div>
    <div class="divider"></div>
    <div class="contact">
      <p class="contact-name">Tomasz Brelwik</p>
      <p class="contact-title">Managing Director</p>
      <p class="contact-address">14-16 Harrow Lane,<br>London, E2 8QT</p>
      <ul class="contact-lines">
        <li>
          <svg viewBox="0 0 16 16" aria-hidden="true"><path d="M4 1l3 3-2 2c1 2 3 4 5 5l2-2 3 3-2 3C7 15 1 9 1 3z" fill="var(--brand-green)"/></svg>
          020 5194 6281
        </li>
        <li>
          <svg viewBox="0 0 16 16" aria-hidden="true"><rect x="4" y="1" width="8" height="14" rx="1.5" fill="none" stroke="var(--brand-green)" stroke-width="1.6"/><circle cx="8" cy="12.5" r="0.9" fill="var(--brand-green)"/></svg>
          07845139072
        </li>
        <li>
          <svg viewBox="0 0 16 16" aria-hidden="true"><rect x="1" y="3" width="14" height="10" fill="none" stroke="var(--brand-green)" stroke-width="1.5"/><path d="M1 3l7 6 7-6" fill="none" stroke="var(--brand-green)" stroke-width="1.5"/></svg>
          tomasz@varkelt.co.uk
        </li>
        <li>
          <svg viewBox="0 0 16 16" aria-hidden="true"><circle cx="8" cy="8" r="6.5" fill="none" stroke="var(--brand-green)" stroke-width="1.4"/><ellipse cx="8" cy="8" rx="3" ry="6.5" fill="none" stroke="var(--brand-green)" stroke-width="1.2"/><path d="M1.5 8h13" stroke="var(--brand-green)" stroke-width="1.2"/></svg>
          www.varkelt.co.uk
        </li>
      </ul>
    </div>
  </section>

</main>
</body>
</html>
```